Bold, Modern, Clean "Kestrelwaymassage.com" website

Why we stand out?
We are a male and female mobile massage team. Our names are Paul and Lina. 
Kestrel Way is a Seattle based mobile massage service. Our massage is offered to the community with a goal of facilitating balance within each individual. We specialize in integrated Pain management, and sports/medical massage therapy. Every client's first assessment is attended by our male and female massage therapist team. Depending on the goals identified for an individual determines which therapist will be assigned to provide treatment, if not both.

Our passion...
Here at Kestrel Way, we have a great passion for Postural Resoration and how it is integrated into an individual's Massage treatment. We pride ourselves in being natural facilitators of healing, which takes the ego of the therapist out of the client's healing process. We strive to deliver the best massage possible by including modalities such as Neuromuscular, Myofascial release, spontaneous muscle release, postural restoration, orthopedic, and medical massage.

Our education...

We are both Graduates of Venmora, school of massage therapy. We have continuing education in medical massage, myofacial release, trigger point therapy, postural restoration, anatomy, and spontaneous muscle release. Lina is also a Certified Yoga Instructor, which amplifies her experience with flexibility and strength as it pertains to each individual. Paul's passion is Massage, stretching, and strength training to encourage postural restoration and realignment.

Our rates-

Our rates are $75/ 60 minutes, $95/ 90 minutes, and $120/ 120 minutes.

Education-
Both Lina and I worked as behavioral health professionals that specialized in life skills mentoring for youth who had experienced different types of trauma. This led us both to want to help others in a different environment, where individuals can be empowered to take responsibility over their own healing. To us, massage is a type of manipulation physical therapy, that encourages healing on many levels.

Advice to any massage client-
The most important thing to 'us', as Licenced providers is to get you on to our table to show you our skills. But a good therapist never forgets that it's not about what we do for you, but what we can facilitate for you. Your health and healing has nothing to do with us. It is yours, not ours. Identify what your goals are with any Therapist, and know what the end looks like. Progress should be tangible, such as range of motion, and decreased pain.

Lina and Paul at Kestrel Way are awesome! I recently had open heart surgery, and Lina worked on me to increase my range of motion while helping with the pinched nerve from my arm being in the same position for so long during my surgery. My wife drives a lot for work, and Paul has helped decrease her neck and lower back pain immensely. They are seriously the best therapists I have ever worked with. I would recommend them to anyone who needs anything from stress relief to a medical massage treatment. They are professional, up beat, easy going, and always on time. And, I love that they meet us where ever we like! We did a staycation recently, where they came to our hotel to give us relaxation massages. Although usually they come to our home, where we focus on pain related issues. We will continue to work with them for a long, long time.

Target Market(s)

Mobile massage therapy clients

Industry/Entity Type

Massage Therapy

Coding

Coded - Design and coding required

Number of Pages Required

1 page

Font styles to use
Serif
Sans Serif

Requirements
Must have
• Please add or remove any information that would help the presentation of our website. Our logo is posted below, please include into the website.
• Please include a contact field that includes, kestrelwaymassage@fernmail.net,
• (206) 555-0148
• We have also included our own stock photos, as well as a photo of Paul and Lina. Please include a cropped photo of both massage therapists.

```html
<!DOCTYPE html>
<html lang="en">
<head>
<meta charset="utf-8">
<title>Kestrel Way – Mobile Massage</title>
<link href="https://fonts.googleapis.com/css2?family=Maven+Pro:wght@400;500;600;700&family=Open+Sans:ital,wght@0,400;0,600;1,400&display=swap" rel="stylesheet">
<style>
:root{
  --navy:#232a6a;
  --blue:#1190c4;
  --ink:#1d1d22;
  --muted:#8a8f98;
  --line:#e3e5e8;
  --soft:#f6f6f7;
  --white:#ffffff;
  --foot-top:#2c2c2e;
  --foot-bot:#121213;
}
*{margin:0;padding:0;box-sizing:border-box}
html,body{width:1200px;height:2184px;overflow:hidden;background:var(--white)}
body{position:relative;font-family:"Open Sans",sans-serif;color:var(--ink)}
.abs{position:absolute}

/* header */
.site-header{position:absolute;left:0;top:0;width:1200px;height:119px;background:var(--white);z-index:3}
.brand{position:absolute;left:104px;top:44px;display:flex;align-items:center;gap:10px;font-family:"Maven Pro",sans-serif;font-weight:700;font-size:26px;color:var(--navy);white-space:nowrap}
.brand-dot{width:16px;height:16px;border-radius:50%;background:var(--navy);flex:none}
.main-nav{position:absolute;top:45px;left:387px;font-family:"Maven Pro",sans-serif;font-size:13px;color:#2b2b30}
.main-nav a{position:absolute;top:0;height:35px;line-height:35px;white-space:nowrap;color:inherit;text-decoration:none}
.main-nav a.active{background:var(--blue);color:var(--white);width:70px;text-align:center}
.nav-divider{position:absolute;left:966px;top:44px;width:1px;height:42px;background:#c9cbd0}
.quick-label{position:absolute;left:984px;top:42px;font-size:9px;letter-spacing:1px;color:var(--muted);font-family:"Maven Pro",sans-serif}
.quick-phone{position:absolute;left:984px;top:62px;font-size:14px;color:#3a3a40;font-family:"Maven Pro",sans-serif;display:flex;align-items:center;gap:8px}

/* hero */
.hero{position:absolute;left:0;top:119px;width:1200px;height:519px;background:linear-gradient(110deg,#5a3a24 0%,#b67c52 28%,#d69c6e 45%,#8a5532 65%,#4a2c1a 85%,#3a2416 100%)}
.hero-caption{position:absolute;left:98px;font-family:"Maven Pro",sans-serif;font-weight:600;font-size:19px;color:var(--white);background:rgba(35,32,80,.82);padding:0 22px;height:40px;line-height:40px;letter-spacing:.5px}
.hero-cta{position:absolute;left:98px;top:531px;width:202px;height:41px;background:var(--blue);color:var(--white);font-family:"Maven Pro",sans-serif;font-weight:600;font-size:19px;letter-spacing:1px;line-height:41px;text-align:center}
.slider-dots{position:absolute;left:578px;top:611px;display:flex;gap:6px}
.slider-dots span{width:7px;height:7px;border-radius:50%;background:var(--white)}
.slider-dots span.on{background:var(--blue)}

/* welcome */
.welcome-title{position:absolute;top:682px;left:0;width:1200px;text-align:center;font-family:"Maven Pro",sans-serif;font-weight:600;font-size:23px;letter-spacing:2px}
.welcome-sub{position:absolute;top:710px;left:0;width:1200px;text-align:center;font-family:"Maven Pro",sans-serif;font-size:18px;color:#33333a}
.feature{position:absolute;top:830px;width:210px;text-align:center}
.feature-icon{height:60px;display:flex;align-items:center;justify-content:center}
.feature h3{font-family:"Maven Pro",sans-serif;font-weight:600;font-size:14px;letter-spacing:1.5px;margin-top:21px}
.feature p{font-size:10.5px;line-height:15px;color:var(--muted);margin-top:9px;text-align:justify;text-align-last:center}
.btn-small{display:inline-block;margin-top:14px;background:var(--blue);color:var(--white);font-family:"Maven Pro",sans-serif;font-size:12px;width:90px;height:25px;line-height:25px}

/* about */
.about{position:absolute;left:0;top:1079px;width:1200px;height:377px;background:var(--soft)}
.about-photo{position:absolute;left:170px;top:77px;width:222px;height:222px;border-radius:50%;border:4px solid var(--white);background:radial-gradient(circle at 45% 40%,#d8cfc6,#a89a8e 60%,#e9e6e2)}
.about-kicker{position:absolute;left:451px;top:77px;font-family:"Maven Pro",sans-serif;font-size:19px;letter-spacing:1.5px;color:#2b2b30}
.about-title{position:absolute;left:451px;top:102px;font-family:"Maven Pro",sans-serif;font-weight:600;font-size:19px;letter-spacing:2px}
.about-rule{position:absolute;left:451px;top:162px;width:215px;height:1px;background:#d8dade}
.about-rule::before{content:"";position:absolute;left:0;top:-1px;width:76px;height:3px;background:var(--navy)}
.about-text{position:absolute;left:451px;top:194px;width:580px;font-size:11.5px;line-height:27px;color:var(--muted)}

/* testimonials & contact */
.section-kicker{position:absolute;top:1514px;width:460px;text-align:center;font-family:"Maven Pro",sans-serif;font-size:19px;letter-spacing:1.5px;color:#55585f}
.section-title{position:absolute;top:1540px;width:460px;text-align:center;font-family:"Maven Pro",sans-serif;font-weight:600;font-size:19px;letter-spacing:2px}
.testimonial-card{position:absolute;left:99px;top:1612px;width:454px;height:304px;background:var(--navy);border-radius:3px;color:var(--white);text-align:center}
.round-icon{position:absolute;width:56px;height:56px;border-radius:50%;background:var(--white);border:2px solid #2a2a30;display:flex;align-items:center;justify-content:center}
.testimonial-card .round-icon{left:199px;top:-28px}
.t-name{position:absolute;top:52px;width:100%;font-family:"Maven Pro",sans-serif;font-weight:500;font-size:17px}
.t-role{position:absolute;top:73px;width:100%;font-size:10.5px}
.t-rule{position:absolute;left:102px;width:282px;height:1px;background:rgba(255,255,255,.35)}
.t-quote{position:absolute;left:34px;top:140px;width:386px;font-style:italic;font-size:11.5px;line-height:19px}
.t-dots{position:absolute;left:203px;top:264px;display:flex;gap:6px}
.t-dots span{width:9px;height:9px;border-radius:50%;background:var(--white)}
.t-dots span.on{background:var(--blue)}
.contact-card{position:absolute;left:647px;top:1612px;width:454px;height:304px;background:var(--soft);border-radius:3px}
.contact-card .round-icon{left:199px;top:-28px}
.field{position:absolute;background:var(--white);border:1px solid #eceef0;font-size:10px;color:#9aa0a8;padding:7px 9px}
.btn-submit{position:absolute;left:187px;top:252px;width:79px;height:28px;background:var(--blue);color:var(--white);font-family:"Maven Pro",sans-serif;font-weight:600;font-size:13px;line-height:28px;text-align:center;letter-spacing:.5px}

/* footer */
.site-footer{position:absolute;left:0;top:2002px;width:1200px;height:182px;background:linear-gradient(var(--foot-top),var(--foot-bot))}
.footer-nav{position:absolute;left:100px;top:36px;display:flex;align-items:center;font-size:12px;color:#e8e8ea}
.footer-nav .pill{border:1px solid #e8e8ea;border-radius:14px;padding:4px 15px}
.footer-nav .sep{margin:0 14px;color:#bbb}
.socials{position:absolute;left:1006px;top:38px;display:flex;gap:14px}
.socials span{width:13px;height:13px;border-radius:50%;background:#e8e8ea}
.social-tip{position:absolute;left:1010px;top:68px;width:64px;height:22px;border-radius:11px;background:var(--blue);color:var(--white);font-size:8px;font-weight:600;line-height:22px;text-align:center;letter-spacing:.5px}
.footer-rule{position:absolute;left:100px;top:99px;width:1013px;height:1px;background:#3a3a3d}
.footer-info{position:absolute;top:116px;display:flex;align-items:center;gap:10px;font-size:10.5px;line-height:14px;color:#e8e8ea}
.info-dot{width:22px;height:22px;border-radius:50%;background:#f2f2f2;display:flex;align-items:center;justify-content:center;flex:none}
.copyright{position:absolute;right:87px;top:126px;font-size:10.5px;color:#e8e8ea}
</style>
</head>
<body>

<header class="site-header">
  <div class="brand"><span class="brand-dot"></span>Kestrel Way</div>
  <nav class="main-nav">
    <a class="active" style="left:0">Home</a>
    <a style="left:88px">About Us</a>
    <a style="left:171px">Service</a>
    <a style="left:249px">Gallery</a>
    <a style="left:327px">Clients</a>
    <a style="left:402px">Testimonials</a>
    <a style="left:516px">Contact</a>
  </nav>
  <div class="nav-divider"></div>
  <div class="quick-label">FOR QUICK CONTACT</div>
  <div class="quick-phone">
    <svg width="9" height="14" viewBox="0 0 9 14"><rect x="0.8" y="0.8" width="7.4" height="12.4" rx="1.5" fill="none" stroke="#3a3a40" stroke-width="1.4"/><circle cx="4.5" cy="11" r=".9" fill="#3a3a40"/></svg>
    (206) 555-0148
  </div>
</header>

<section class="hero" role="img" aria-label="Photo of a therapist's hands giving a back massage beside a tray of massage stones, candle and cream"></section>
<div class="hero-caption" style="top:432px">Mobile Massage company that specializes in sports and</div>
<div class="hero-caption" style="top:478px">medical massage therapy.</div>
<div class="hero-cta">GET A QUOTE</div>
<div class="slider-dots"><span class="on"></span><span></span><span></span><span></span></div>

<h1 class="welcome-title">WELCOME</h1>
<p class="welcome-sub">Integer vitae libero ac risus egestas placerat</p>
<svg class="abs" style="left:390px;top:768px" width="396" height="14" viewBox="0 0 396 14">
  <line x1="0" y1="8" x2="396" y2="8" stroke="#e3e5e8"/>
  <polyline points="112,8 197,8 207,16 217,8 284,8" fill="none" stroke="#1190c4" stroke-width="1.3"/>
</svg>

<div class="feature" style="left:90px">
  <div class="feature-icon">
    <svg width="58" height="46" viewBox="0 0 58 46"><circle cx="17" cy="12" r="7" fill="#c7cbd1"/><circle cx="41" cy="12" r="7" fill="#c7cbd1"/><path d="M4 40c0-10 6-16 13-16s13 6 13 16z" fill="#c7cbd1"/><path d="M28 40c0-10 6-16 13-16s13 6 13 16z" fill="#c7cbd1"/><circle cx="29" cy="18" r="8" fill="#1190c4"/><path d="M14 46c0-11 7-17 15-17s15 6 15 17z" fill="#1190c4"/></svg>
  </div>
  <h3>WHY WE STAND OUT?</h3>
  <p>We are a male and female mobile massage team. Our names are Paul and Lina. Kestrel Way is a Seattle based mobile massage service.</p>
</div>
<div class="feature" style="left:360px">
  <div class="feature-icon">
    <svg width="82" height="82" viewBox="0 0 82 82" style="margin-top:-14px"><circle cx="41" cy="41" r="40" fill="#232a6a"/><path d="M22 44l12-12 8 4 10-8 10 10-14 14-6-4-6 6z" fill="#fff"/><path d="M34 40l8 8M38 36l8 8" stroke="#232a6a" stroke-width="2"/></svg>
  </div>
  <h3>OUR PASSION...</h3>
  <p>Here at Kestrel Way, we have a great passion for Postural Resoration and how it is integrated into an individual's Massage treatment.</p>
  <span class="btn-small">READ MORE</span>
</div>
<div class="feature" style="left:630px">
  <div class="feature-icon">
    <svg width="62" height="40" viewBox="0 0 62 40"><path d="M31 4l29 12-29 12L2 16z" fill="#1190c4"/><path d="M14 22v10c0 4 8 7 17 7s17-3 17-7V22l-17 7z" fill="#1190c4"/><path d="M56 17v14" stroke="#1190c4" stroke-width="2"/></svg>
  </div>
  <h3>OUR EDUCATION...</h3>
  <p>We are both Graduates of Venmora, school of massage therapy. We have continuing education in medical massage, myofacial release,</p>
</div>
<div class="feature" style="left:904px">
  <div class="feature-icon">
    <svg width="48" height="48" viewBox="0 0 48 48"><path d="M26 6h14v14L20 40 6 26z" fill="#1190c4"/><circle cx="33" cy="13" r="3" fill="#fff"/><path d="M33 13c4-8 12-6 10 2" fill="none" stroke="#1190c4" stroke-width="2"/></svg>
  </div>
  <h3>OUR RATES-</h3>
  <p>Our rates are $75/ 60 minutes, $95/ 90 minutes, and $120/ 120 minutes.</p>
</div>

<section class="about">
  <div class="about-photo" role="img" aria-label="Photo of a therapist giving a massage to a client lying on a table"></div>
  <div class="about-kicker">Lorem ipsum dolor sit</div>
  <h2 class="about-title">ABOUT US</h2>
  <div class="about-rule"></div>
  <p class="about-text">Praesent dapibus, neque id cursus faucibus, tortor neque egestas augue, eu vulputate magna eros eu erat. Aliquam erat volutpat. Nam dui mi, tincidunt quis, accumsan porttitor, facilisis luctus, metus sectetuer ligula vulputate sem tristique cursus. Nam nulla quam, gravida non, commodo a, sodales sit in, pharetra a, ultricies in, diam. Sed arcu. Cras consequat</p>
</section>

<div class="section-kicker" style="left:114px">Our Clients</div>
<h2 class="section-title" style="left:114px">TESTIMONIALS</h2>
<div class="section-kicker" style="left:628px">Contact Us</div>
<h2 class="section-title" style="left:628px">QUICK CONTACT</h2>

<div class="testimonial-card">
  <div class="round-icon"><svg width="26" height="28" viewBox="0 0 26 28"><circle cx="13" cy="9" r="7" fill="none" stroke="#232a6a" stroke-width="1.6"/><path d="M2 27c0-7 5-11 11-11s11 4 11 11" fill="none" stroke="#232a6a" stroke-width="1.6"/></svg></div>
  <div class="t-name">Jhone Doe</div>
  <div class="t-role">Lorem ipsum dolor</div>
  <div class="t-rule" style="top:114px"></div>
  <p class="t-quote">Lina and Paul at Kestrel Way are awesome! I recently had open heart surgery, and Lina worked on me to increase my range of motion while helping with the pinched nerve from my arm being in the same position for so long during my surgery.</p>
  <div class="t-rule" style="top:242px"></div>
  <div class="t-dots"><span class="on"></span><span></span><span></span></div>
</div>

<div class="contact-card">
  <div class="round-icon"><svg width="26" height="20" viewBox="0 0 26 20"><rect x="1" y="1" width="24" height="18" fill="none" stroke="#2a2a30" stroke-width="1.6"/><path d="M1 1l12 10 12-10" fill="none" stroke="#2a2a30" stroke-width="1.6"/></svg></div>
  <div class="field" style="left:26px;top:53px;width:191px;height:28px">First name...</div>
  <div class="field" style="left:236px;top:53px;width:190px;height:28px">Last name...</div>
  <div class="field" style="left:26px;top:99px;width:191px;height:28px">Phone...</div>
  <div class="field" style="left:236px;top:99px;width:190px;height:28px">Email...</div>
  <div class="field" style="left:26px;top:146px;width:400px;height:89px">Message...</div>
  <div class="btn-submit">SUBMIT</div>
</div>

<footer class="site-footer">
  <nav class="footer-nav">
    <span class="pill">Home</span><span style="margin-left:18px">About Us</span><span class="sep">|</span><span>Service</span><span class="sep">|</span><span>Gallery</span><span class="sep">|</span><span>Clients</span><span class="sep">|</span><span>Testimonials</span><span class="sep">|</span><span>Contact</span>
  </nav>
  <div class="socials"><span></span><span></span><span></span><span></span></div>
  <div class="social-tip">SHAREFOLIO</div>
  <div class="footer-rule"></div>
  <div class="footer-info" style="left:100px">
    <span class="info-dot"><svg width="10" height="13" viewBox="0 0 10 13"><path d="M5 13S0 7 0 5a5 5 0 0110 0c0 2-5 8-5 8z" fill="#1d1d22"/><circle cx="5" cy="5" r="2" fill="#f2f2f2"/></svg></span>
    <span>yoursite, 48 Alder Lane<br>Rd1, Northfield, 7720</span>
  </div>
  <div class="footer-info" style="left:280px">
    <span class="info-dot"><svg width="11" height="11" viewBox="0 0 11 11"><path d="M2 0l2 3-1 1.5c.8 1.6 2 2.8 3.5 3.5L8 7l3 2-1 2C5 11 0 6 0 1z" fill="#1d1d22"/></svg></span>
    <span>(206) 555-0148</span>
  </div>
  <div class="footer-info" style="left:412px">
    <span class="info-dot"><svg width="11" height="9" viewBox="0 0 11 9"><rect width="11" height="9" fill="#1d1d22"/><path d="M0 0l5.5 5L11 0" fill="none" stroke="#f2f2f2"/></svg></span>
    <span><b style="font-weight:600">EMAIL:</b> studio@harbordesk.net</span>
  </div>
  <div class="copyright">©Copyright 2015 yoursite. All Rights Reserved.</div>
</footer>

</body>
</html>
```